Quorva - corporate Business Card

We need a good look and innovative business card for a new start up company based in Los Angeles called "Quorva". We are in a payment business, including payment card, app, and ewallet. We are expert in online payment and Card not present (CNP) transaction.
We need an innovative, modern business card.

Our logo font is Aero Matics

Target Market(s)

Startup - Bank - Online Payment - Card Manufacturing

Industry/Entity Type

Startup

Contact Information for Business Card

phone: 555 014 7396 - Address: 4172 Marlowe blvd, Cylver City, CA 90299

Requirements
Must have
• Message: innovative, professional, expert, high tech, trust, online payment expert, security
Nice to have
• no comment
Should not have
• no Comment

```html
<!DOCTYPE html>
<html lang="en">
<head>
<meta charset="utf-8">
<title>Quorva — Business Card</title>
<link href="https://fonts.googleapis.com/css2?family=Exo+2:wght@500&family=Arimo:wght@400;700&display=swap" rel="stylesheet">
<style>
  :root {
    --backdrop: #2b2b2d;
    --card-white: #ffffff;
    --brand-red: #c41f30;
    --brand-red-dark: #a8192a;
    --logo-red: #c8363f;
    --ink-white: #ffffff;
    --edge-shadow: rgba(0,0,0,0.45);
  }
  * { margin: 0; padding: 0; box-sizing: border-box; }
  html, body { width: 1200px; height: 950px; overflow: hidden; }
  body {
    background: var(--backdrop);
    display: flex;
    flex-direction: column;
    align-items: center;
    justify-content: center;
    gap: 70px;
  }
  .card {
    position: relative;
    width: 600px;
    height: 343px;
    background: var(--card-white);
    box-shadow: 0 12px 30px var(--edge-shadow);
    overflow: hidden;
  }
  .card-shape { position: absolute; inset: 0; width: 100%; height: 100%; }
  .brand {
    position: absolute;
    display: flex;
    align-items: center;
    gap: 12px;
    font-family: "Exo 2", sans-serif;
    font-weight: 500;
    color: var(--logo-red);
    letter-spacing: 1px;
    line-height: 1;
  }
  .brand-dot { border-radius: 50%; background: var(--logo-red); flex: none; }
  .card--info .brand { left: 46px; top: 148px; font-size: 52px; }
  .card--info .brand-dot { width: 52px; height: 52px; }
  .card--logo .brand { left: 50%; top: 50%; transform: translate(-50%, -50%); font-size: 78px; }
  .card--logo .brand-dot { width: 82px; height: 82px; }
  .contact {
    position: absolute;
    right: 26px;
    top: 34px;
    width: 220px;
    color: var(--ink-white);
    font-family: "Arimo", sans-serif;
    text-align: right;
  }
  .contact-name { font-weight: 700; font-size: 19px; }
  .contact-role { font-size: 13px; margin-bottom: 26px; }
  .contact-address { font-size: 12px; line-height: 1.35; margin-bottom: 16px; padding-right: 26px; }
  .contact-line {
    display: flex;
    justify-content: flex-end;
    align-items: center;
    gap: 8px;
    font-size: 12px;
    margin-bottom: 9px;
  }
  .contact-icon { width: 16px; height: 16px; flex: none; }
</style>
</head>
<body>

  <section class="card card--info">
    <svg class="card-shape" viewBox="0 0 600 343" preserveAspectRatio="none" aria-hidden="true">
      <path d="M330 0 C300 110 300 220 350 343 L600 343 L600 0 Z" fill="var(--brand-red)"/>
      <path d="M352 0 C325 90 322 190 360 300" stroke="var(--ink-white)" stroke-width="3" fill="none" opacity="0.85"/>
      <path d="M346 0 C318 100 316 210 352 320" stroke="var(--card-white)" stroke-width="1.2" fill="none" opacity="0.5"/>
    </svg>

    <div class="brand">
      <span class="brand-dot"></span>
      <span class="brand-name">quorva</span>
    </div>

    <div class="contact">
      <p class="contact-name">Marcus Venn</p>
      <p class="contact-role">President</p>
      <p class="contact-address">4172 Marlowe blvd<br>Cylver City, CA 90299</p>
      <p class="contact-line">555 014 7396
        <svg class="contact-icon" viewBox="0 0 16 16" aria-hidden="true"><rect width="16" height="16" rx="3" fill="var(--ink-white)"/><path d="M5 3.5 L7 6 L6 7.5 Q7.5 9.5 8.5 10 L10 9 L12.5 11 L11.5 12.5 Q7 12 3.5 5 Z" fill="var(--brand-red)"/></svg>
      </p>
      <p class="contact-line">marcus@quorva.com
        <svg class="contact-icon" viewBox="0 0 16 16" aria-hidden="true"><rect width="16" height="16" rx="3" fill="var(--ink-white)"/><rect x="3" y="4.5" width="10" height="7" fill="none" stroke="var(--brand-red)" stroke-width="1.3"/><path d="M3 4.5 L8 8.5 L13 4.5" fill="none" stroke="var(--brand-red)" stroke-width="1.3"/></svg>
      </p>
      <p class="contact-line">www.quorva.com
        <svg class="contact-icon" viewBox="0 0 16 16" aria-hidden="true"><circle cx="8" cy="8" r="8" fill="var(--ink-white)"/><circle cx="8" cy="8" r="4.5" fill="none" stroke="var(--brand-red)" stroke-width="1.2"/><path d="M3.5 8 H12.5 M8 3.5 V12.5" stroke="var(--brand-red)" stroke-width="1.1"/></svg>
      </p>
    </div>
  </section>

  <section class="card card--logo">
    <div class="brand">
      <span class="brand-dot"></span>
      <span class="brand-name">quorva</span>
    </div>
  </section>

</body>
</html>
```